Business Card Design Project - 2 sided

We need a business card design for a card having one business on each side (ie. two businesses on one card). Would like a design that incorporates logo, tagline and normal fields (name, position, address, phone).

Would also like an allowance for small font text along the bottom (text to be determined, but less than 50 characters).

NB. Attached logo for Harbor Quill has two variations - either can be used.

www.harborquill-example.com / www.velmaro-example.com

```html
<!DOCTYPE html>
<html lang="en">
<head>
<meta charset="utf-8">
<title>Harbor Quill / Velmaro – Business Card</title>
<link rel="stylesheet" href="https://fonts.googleapis.com/css2?family=Open+Sans:wght@400;600;700&display=swap">
<style>
  :root {
    --backdrop: #ece8e3;
    --card: #ffffff;
    --accent-green: #8cc63f;
    --text-dark: #3d3d3d;
    --text-mid: #555555;
    --text-soft: #999999;
    --shadow: rgba(0, 0, 0, 0.28);
  }
  * { box-sizing: border-box; margin: 0; padding: 0; }
  html, body {
    width: 1200px; height: 487px; overflow: hidden;
    background: var(--backdrop);
    font-family: "Open Sans", Arial, sans-serif;
  }
  .sheet { position: relative; width: 1200px; height: 487px; }
  .card {
    position: absolute; top: 89px; width: 543px; height: 310px;
    background: var(--card);
    box-shadow: 0 3px 8px var(--shadow);
  }
  .card--front { left: 45px; }
  .card--back { left: 611px; }

  .brand { position: absolute; }
  .brand__name {
    font-weight: 600; line-height: 1; color: var(--text-dark);
  }
  .brand__tagline { color: var(--text-mid); white-space: nowrap; }

  .brand--harbor { left: 32px; top: 98px; }
  .brand--harbor .brand__name { font-size: 23px; letter-spacing: 1px; }
  .brand--harbor .brand__tagline { margin-top: 6px; font-size: 9.5px; }

  .brand--velmaro { left: 88px; top: 68px; }
  .brand--velmaro .brand__name { font-size: 30px; letter-spacing: 0.5px; }
  .brand--velmaro .brand__tagline { margin-top: 6px; font-size: 10.5px; letter-spacing: 0.6px; }

  .contacts {
    position: absolute; left: 348px; top: 77px; list-style: none;
  }
  .contacts li {
    display: flex; align-items: center; gap: 8px;
    height: 18.2px; font-size: 13.5px; color: var(--text-dark); white-space: nowrap;
  }
  .contacts svg { width: 10px; height: 10px; flex: none; fill: var(--accent-green); }

  .person {
    position: absolute; left: 38px; top: 215px; white-space: nowrap;
    font-size: 17px; font-weight: 700; color: var(--accent-green);
  }
  .person__title { font-size: 13.5px; font-weight: 400; color: var(--accent-green); }
  .person__title::before { content: "/ "; color: var(--text-soft); }

  .address {
    position: absolute; left: 40px; top: 253px; white-space: nowrap;
    font-size: 13.5px; color: var(--text-dark);
  }
  .fineprint {
    position: absolute; left: 40px; top: 277px; white-space: nowrap;
    font-size: 12.5px; line-height: 1; color: var(--text-mid);
  }
</style>
</head>
<body>
<svg width="0" height="0" style="position:absolute" aria-hidden="true">
  <symbol id="icon-phone" viewBox="0 0 10 10"><path d="M2 0.5 3.6 2.6 2.7 3.6C3.3 5 4.9 6.6 6.4 7.3L7.4 6.4 9.5 8 8.3 9.5C4.5 9.2 0.8 5.5 0.5 1.7Z"/></symbol>
  <symbol id="icon-mobile" viewBox="0 0 10 10"><path d="M2.5 0h5v10h-5z M3.3 1v6.6h3.4V1z"/></symbol>
  <symbol id="icon-fax" viewBox="0 0 10 10"><path d="M1 2.5C3 0.5 7 0.5 9 2.5L8 4 6.5 3.3V2.6C5.5 2.2 4.5 2.2 3.5 2.6V3.3L2 4Z M2 5h6v4H2z"/></symbol>
  <symbol id="icon-mail" viewBox="0 0 10 10"><path d="M0.5 4 5 1 9.5 4v5h-9z"/></symbol>
  <symbol id="icon-web" viewBox="0 0 10 10"><circle cx="5" cy="5" r="4.5"/></symbol>
</svg>

<main class="sheet">
  <section class="card card--front">
    <div class="brand brand--harbor">
      <div class="brand__name">HARBOR QUILL</div>
      <div class="brand__tagline">Website Translation and Localisation Specialist...</div>
    </div>
    <ul class="contacts">
      <li><svg><use href="#icon-phone"/></svg>123-456-7890</li>
      <li><svg><use href="#icon-mobile"/></svg>123-456-7890</li>
      <li><svg><use href="#icon-fax"/></svg>123-456-7890</li>
      <li><svg><use href="#icon-mail"/></svg>name@website.com</li>
      <li><svg><use href="#icon-web"/></svg>www.website.com</li>
    </ul>
    <div class="person">Your Name <span class="person__title">Title</span></div>
    <p class="address">Complex name, Street City, State, zip code</p>
    <p class="fineprint">xxxxxxxxxxxxxxxxxxxxxxxxxxxxxxxxxxxxxxxxxxxxxxxxxx</p>
  </section>

  <section class="card card--back">
    <div class="brand brand--velmaro">
      <div class="brand__name">velmaro</div>
      <div class="brand__tagline">Professional SEO Services</div>
    </div>
    <ul class="contacts">
      <li><svg><use href="#icon-phone"/></svg>123-456-7890</li>
      <li><svg><use href="#icon-mobile"/></svg>123-456-7890</li>
      <li><svg><use href="#icon-fax"/></svg>123-456-7890</li>
      <li><svg><use href="#icon-mail"/></svg>name@website.com</li>
      <li><svg><use href="#icon-web"/></svg>www.website.com</li>
    </ul>
    <div class="person">Your Name <span class="person__title">Title</span></div>
    <p class="address">Complex name, Street City, State, zip code</p>
    <p class="fineprint">xxxxxxxxxxxxxxxxxxxxxxxxxxxxxxxxxxxxxxxxxxxxxxxxxx</p>
  </section>
</main>
</body>
</html>
```